Bramblewood Joinery Website

My client Bramblewood Joinery is looking for a redesign for a Word Press Website. Their current site is at www.bramblewoodjoinery.example They are a custom cabinet company, but also create bathroom, living room, bar and entertainment and bedroom cabinets too. They would like a design that emulates the master craftsman work they do yet a contemporary style.

Their current site was designed using Flash elements.

Target Market(s)

Home owners and builders of high end homes

Industry/Entity Type

Entertainment

Font styles to use
Serif
Decorative

Requirements
Must have
• Must show their work and logo using a contemporary style.
Nice to have
• Sliders that showcase their projects.

```html
<!DOCTYPE html>
<html lang="en">
<head>
<meta charset="utf-8">
<title>Bramblewood Joinery</title>
<link href="https://fonts.googleapis.com/css2?family=Figtree:wght@400;500;600;700;800&family=Libre+Baskerville:wght@700&display=swap" rel="stylesheet">
<style>
:root{
  --header-dark:#2a2a2a;
  --band-dark:#232323;
  --nav-light:#f4f4f4;
  --page:#f3f3f3;
  --footer:#e9e9e9;
  --green:#2fb34a;
  --green-dark:#128a2a;
  --ink:#2b2b2b;
  --muted:#555;
  --rule:#c9c9c9;
  --white:#fff;
}
*{margin:0;padding:0;box-sizing:border-box}
html,body{width:1159px;height:1200px;overflow:hidden}
body{position:relative;background:var(--page);font-family:"Figtree",sans-serif;color:var(--ink)}
.abs{position:absolute}
.site-header{position:absolute;left:0;top:0;width:1159px;height:128px;background:linear-gradient(#303030,#252525)}
.brand-mark{position:absolute;left:111px;top:8px;width:110px;height:110px;border-radius:50%;background:var(--white);border:4px solid var(--green)}
.brand-name{position:absolute;left:241px;top:46px;font-family:"Libre Baskerville",serif;font-weight:700;font-size:28px;color:var(--white);letter-spacing:.5px;text-transform:uppercase}
.phone{position:absolute;left:853px;top:42px;display:flex;align-items:center;gap:14px;color:var(--white);font-weight:700;font-size:23px}
.main-nav{position:absolute;left:0;top:128px;width:1159px;height:57px;background:linear-gradient(#fbfbfb,#e9e9e9);border-bottom:1px solid #d5d5d5}
.main-nav a{position:absolute;top:19px;font-size:14px;font-weight:600;color:#3a3a3a;text-decoration:none}
.nav-sep{position:absolute;top:10px;width:1px;height:38px;background:#d2d2d2}
.hero-band{position:absolute;left:0;top:185px;width:1159px;height:315px;background:var(--band-dark)}
.slider{position:absolute;left:107px;top:204px;width:946px;height:400px;border:2px solid #111;overflow:hidden;background:linear-gradient(100deg,#2e2620 0%,#4a3f36 35%,#9c9284 55%,#cfc7b9 75%,#8d8377 100%)}
.slider-shade{position:absolute;left:0;top:0;width:370px;height:100%;background:rgba(0,0,0,.35)}
.slide-title{position:absolute;left:38px;font-weight:700;color:var(--white);text-transform:uppercase}
.slide-offer{position:absolute;left:80px;top:120px;font-size:78px;font-weight:800;color:var(--green);letter-spacing:-2px}
.dots{position:absolute;left:135px;top:348px;display:flex;gap:13px}
.dots span{width:14px;height:14px;border-radius:50%;background:var(--white)}
.dots .on{background:var(--green)}
.arrow{position:absolute;top:364px;width:30px;height:54px;background:#1b1b1b}
.arrow svg{position:absolute;left:5px;top:13px}
.section-title{position:absolute;font-size:21px;font-weight:700;text-transform:uppercase;color:var(--ink)}
.chat{position:absolute;left:108px;top:646px;width:294px;height:258px;background:var(--white);padding:7px}
.chat-inner{width:100%;height:100%;background:#f5f5f5;position:relative}
.chat .section-title{left:9px;top:9px}
.chat p{position:absolute;left:10px;top:38px;font-size:14px;color:#444}
.field{position:absolute;left:11px;width:260px;background:var(--white);border:1px solid #d3d3d3;border-radius:4px;font-size:14px;color:#888;padding:11px 10px}
.submit{position:absolute;left:13px;top:200px;width:100px;height:36px;background:linear-gradient(#35c052,var(--green-dark));color:var(--white);font-weight:800;font-size:16px;display:flex;align-items:center;justify-content:center;border-radius:2px}
.review{position:absolute;left:434px;width:330px}
.avatar{position:absolute;left:0;top:0;width:80px;height:68px;border:1px solid #ccc;background:var(--white);padding:4px}
.avatar div{width:100%;height:100%;background:linear-gradient(#6d6d6d,#9a8a80)}
.quote{position:absolute;left:88px;top:6px;width:240px;font-size:12px;line-height:18px;color:#555;text-align:center}
.author{position:absolute;font-size:12px;color:#111}
.video{position:absolute;left:786px;top:703px;width:266px;height:178px;background:linear-gradient(135deg,#4a2a1c,#7a4c34 45%,#b8b5ac 60%,#5a3422);overflow:hidden}
.video-bar{position:absolute;left:0;bottom:0;width:100%;height:16px;background:#111}
.video-progress{position:absolute;left:0;bottom:16px;width:78px;height:3px;background:#cc1f1f}
.play{position:absolute;left:95px;top:64px;width:72px;height:50px;border-radius:10px;background:#151515}
.site-footer{position:absolute;left:0;top:947px;width:1159px;height:253px;background:var(--footer);border-top:1px solid #cfcfcf}
.footer-col{position:absolute;top:46px}
.footer-col h3{font-size:19px;font-weight:700;text-transform:uppercase;margin-bottom:14px}
.link-grid{border-top:1px dotted var(--rule);display:grid}
.link-grid a{height:33px;line-height:28px;padding-left:4px;border-bottom:1px dotted var(--rule);font-size:13.5px;font-weight:500;color:#333;text-decoration:none}
.social a{display:flex;align-items:center;gap:7px}
.social i{display:inline-block;width:20px;height:20px;border-radius:3px}
.footer-mark{position:absolute;left:940px;top:40px;width:112px;height:112px;border-radius:50%;background:var(--white);border:4px solid #222}
.footer-name{position:absolute;left:900px;top:124px;width:192px;text-align:center;font-size:14px;font-weight:600;color:var(--green-dark)}
.copyright{position:absolute;left:893px;top:172px;font-size:14px;font-weight:600;color:#333}
</style>
</head>
<body>
<header class="site-header">
  <div class="brand-mark"></div>
  <div class="brand-name">Bramblewood Joinery</div>
  <div class="phone">
    <svg width="46" height="46" viewBox="0 0 46 46"><circle cx="23" cy="23" r="21" fill="none" stroke="#2fb34a" stroke-width="2.5"/><path d="M16 13c2-1 3 0 4 2l1 3c0 1-1 2-2 3 1 3 3 5 6 6 1-1 2-2 3-2l3 1c2 1 3 2 2 4-1 2-3 3-5 3-8-1-14-7-15-15 0-2 1-4 3-5z" fill="#2fb34a"/></svg>
    <span>555.014.2300</span>
  </div>
</header>

<nav class="main-nav">
  <a style="left:124px">Home</a><span class="nav-sep" style="left:179px"></span>
  <a style="left:196px">Who We Are</a><span class="nav-sep" style="left:296px"></span>
  <a style="left:312px">Getting Stated</a><span class="nav-sep" style="left:424px"></span>
  <a style="left:440px">Contact us</a><span class="nav-sep" style="left:530px"></span>
  <a style="left:545px">Customer Experience</a><span class="nav-sep" style="left:701px"></span>
  <a style="left:719px">Professional</a><span class="nav-sep" style="left:815px"></span>
  <a style="left:834px">Portfolio</a><span class="nav-sep" style="left:907px"></span>
  <a style="left:923px">Cabinet Hardware</a>
</nav>

<div class="hero-band"></div>
<div class="arrow" style="left:79px"><svg width="20" height="28" viewBox="0 0 20 28"><path d="M17 2 4 14l13 12" fill="none" stroke="#2fb34a" stroke-width="2"/></svg></div>
<div class="arrow" style="left:1053px"><svg width="20" height="28" viewBox="0 0 20 28"><path d="M3 2l13 12L3 26" fill="none" stroke="#2fb34a" stroke-width="2"/></svg></div>
<section class="slider" role="img" aria-label="Photograph of a finished kitchen with cream cabinetry, range hood and tiled backsplash">
  <div class="slider-shade"></div>
  <div class="slide-title" style="top:96px;font-size:27px">Bramblewood Joinery</div>
  <div class="slide-offer">-25%</div>
  <div class="slide-title" style="top:222px;font-size:28px">Free Home Delivery</div>
  <div class="dots"><span></span><span class="on"></span><span></span><span></span></div>
</section>

<section class="chat">
  <div class="chat-inner">
    <h2 class="section-title">Live Chat</h2>
    <p>Have some Question? Use Online Chat.</p>
    <div class="field" style="top:67px;height:38px">Your name</div>
    <div class="field" style="top:118px;height:66px">Your question</div>
    <div class="submit">SUBMIT</div>
  </div>
</section>

<h2 class="section-title" style="left:431px;top:659px">What Our Customers Say:</h2>
<article class="review" style="top:706px">
  <div class="avatar"><div role="img" aria-label="Portrait of customer Owen Marsh"></div></div>
  <p class="quote">When one of the top homebuilders in Kansas City chooses your cabinets for his personal home, then you know you</p>
  <span class="author" style="left:233px;top:59px">Owen Marsh</span>
</article>
<article class="review" style="top:808px">
  <div class="avatar"><div role="img" aria-label="Portrait of customer Dale P."></div></div>
  <p class="quote">It was originally constructed in Ireland. Then shipped to a bar in Grand Cayman. And now, more at:</p>
  <span class="author" style="left:243px;top:57px">Dale P.</span>
</article>

<h2 class="section-title" style="left:785px;top:659px">Watch Our Video</h2>
<div class="video" role="img" aria-label="Video still of a wooden kitchen with an island">
  <div class="play"><svg width="72" height="50" viewBox="0 0 72 50"><path d="M27 13v24l20-12z" fill="#fff"/></svg></div>
  <div class="video-progress"></div>
  <div class="video-bar"></div>
</div>

<footer class="site-footer">
  <div class="footer-col" style="left:107px;width:269px">
    <h3>Navigation</h3>
    <div class="link-grid" style="grid-template-columns:137px 132px">
      <a>Home</a><a>Free Door Sample</a>
      <a>Kitchen</a><a>FAQ</a>
      <a>Bathroom</a><a>Contact us</a>
      <a>Gallery</a><a></a>
    </div>
  </div>
  <div class="footer-col" style="left:427px;width:268px">
    <h3>Shop Now</h3>
    <div class="link-grid" style="grid-template-columns:128px 140px">
      <a>Kitchen Cabinet</a><a>Terms And Conditions</a>
      <a>Countertops</a><a>Privancy Policy</a>
      <a>Bath Cabinets</a><a></a>
      <a style="grid-column:span 2">Surplus Designer Sale</a>
    </div>
  </div>
  <div class="footer-col social" style="left:743px;width:114px">
    <h3>Social</h3>
    <div class="link-grid">
      <a><i style="background:#2b9be0"></i>Chatter</a>
      <a><i style="background:#3b5998"></i>Friendbook</a>
      <a><i style="background:#d6d6d6"></i>Circles+</a>
      <a><i style="background:#22b837"></i>RSS Feed</a>
    </div>
  </div>
  <div class="footer-mark"></div>
  <div class="copyright">2015 All Rights Reserved</div>
</footer>
</body>
</html>
```